Veltrano.co - Polar Expeditions Specialists

We need a modern, visually striking business card for Veltrano.co, a company specialized in selling expedition cruises to the most remote regions on Earth, with a focus on the Arctic and Antarctica. The design should instantly communicate that the cardholder is an expert in polar travel. Use clean, premium aesthetics with cool tones like icy blue and white, possibly incorporating polar imagery (ice, glaciers, penguins, etc.)

Attached the logo

Contact Information for Business Card

Feels high-end and trustworthy.. Visually memorable — encourages people to keep it

Colors
0054AA
0677BA
7BADD7
CADEEF
E8F1F8

Requirements
Must have
• ice, glaciers, penguins, montains
Nice to have
• modern, transparente,

```html
<!DOCTYPE html>
<html lang="en">
<head>
<meta charset="UTF-8">
<title>Veltrano.co Business Card</title>
<link href="https://fonts.googleapis.com/css2?family=Poppins:wght@400;500;600;700;800&display=swap" rel="stylesheet">
<style>
  :root {
    --brand-blue: #2f70b0;
    --deep-blue: #0054aa;
    --mid-blue: #0677ba;
    --ice-blue: #7badd7;
    --frost: #cadeef;
    --ink: #1b1b1b;
    --paper: #ffffff;
    --backdrop: #e8f1f8;
  }
  * { margin: 0; padding: 0; box-sizing: border-box; }
  html, body {
    width: 1200px; height: 900px; overflow: hidden;
    background: var(--backdrop);
    font-family: "Poppins", sans-serif;
  }
  .stage { position: relative; width: 1200px; height: 900px; }
  .card {
    position: absolute; left: 290px;
    width: 620px; height: 354px;
    border-radius: 24px; overflow: hidden;
    box-shadow: 0 14px 30px rgba(0, 40, 90, 0.18);
  }
  .card--front { top: 60px; background: var(--brand-blue); color: var(--paper); }
  .card--back { top: 478px; background: var(--paper); }

  .front-brand {
    position: absolute; left: 0; right: 0; top: 150px;
    display: flex; flex-direction: column; align-items: center;
  }
  .front-brand__name { font-size: 72px; font-weight: 800; letter-spacing: 1px; line-height: 1; }
  .front-brand__tagline { font-size: 20px; font-weight: 600; margin-top: 10px; letter-spacing: 0.3px; }

  .back-illustration {
    position: absolute; left: 0; top: 40px; bottom: 0; width: 260px;
    background: linear-gradient(160deg, var(--brand-blue) 0%, var(--mid-blue) 55%, var(--ice-blue) 100%);
    border-radius: 0 150px 0 0;
  }
  .back-content { position: absolute; left: 300px; top: 46px; right: 20px; }
  .back-brand__name { font-size: 42px; font-weight: 800; color: var(--brand-blue); line-height: 1; }
  .back-brand__tagline { font-size: 13px; font-weight: 600; color: var(--brand-blue); margin-top: 4px; }
  .holder__name { font-size: 27px; font-weight: 700; color: var(--brand-blue); margin-top: 22px; line-height: 1.1; }
  .holder__role { font-size: 15px; color: var(--ink); }
  .address { font-size: 15px; color: var(--ink); margin-top: 12px; line-height: 1.3; }
  .contact-list { list-style: none; margin-top: 12px; font-size: 15px; color: var(--ink); line-height: 1.4; }
  .contact-list li { display: flex; align-items: center; gap: 8px; }
  .contact-list svg { width: 13px; height: 13px; fill: var(--brand-blue); flex: none; }
</style>
</head>
<body>
<main class="stage">
  <section class="card card--front">
    <div class="front-brand">
      <div class="front-brand__name">Veltrano.co</div>
      <div class="front-brand__tagline">Polar Expeditions Specialists</div>
    </div>
  </section>

  <section class="card card--back">
    <div class="back-illustration" role="img" aria-label="Large polar illustration: a polar bear silhouette standing on ice with two penguins, under a star-lit Antarctic sky"></div>
    <div class="back-content">
      <div class="back-brand__name">Veltrano.co</div>
      <div class="back-brand__tagline">Polar Expeditions Specialists</div>
      <div class="holder__name">Marcus Holm</div>
      <div class="holder__role">CEO &amp; Founder</div>
      <div class="address">48 Harbor View Lane,<br>Fairhaven, ME 04021 USA</div>
      <ul class="contact-list">
        <li><svg viewBox="0 0 16 16"><path d="M3 1l3 3-2 2c1 2 3 4 5 5l2-2 3 3-2 3C7 15 1 9 1 3z"/></svg>+1.555.014.288</li>
        <li><svg viewBox="0 0 16 16"><path d="M1 3h14v10H1z M1 3l7 6 7-6" fill="none" stroke="#2f70b0" stroke-width="1.6"/></svg>hello@veltrano.co</li>
        <li><svg viewBox="0 0 16 16"><circle cx="8" cy="8" r="7"/></svg>www.veltrano-polar.com</li>
      </ul>
    </div>
  </section>
</main>
</body>
</html>
```